New Business Card for Software Company

We are looking at rebranding a 10 year old company that specializes in PDF and DWF solutions for Architects and Engineers. We will attach the new company logo that we are going with so you can work with that and complimentary colors.
The sample information we would like on the business card is:
Gerald Pinfold
Vice President
4738 W. Harrowgate Lane. STE 305
PMB#417
Mesa, AZ 85374
866-392-5074 US Toll Free
123-456-3190 Cell
gpinfold@plavorix.com
The old tag line that we had on the business cars was.
Delivering Dependable Drawing Tools for Architects and Engineers Across Every Project Site.
If you have an idea for a better tag line we are open to that also.
Updates
We would like to thank all of the Designers for their wonderful work. We apologize that we will not have the time to provide feedback to everyone. There is just so many innovative and professional designs that you have all created making our decision even harder.
Target Market(s)
Architects and Engineers
Industry/Entity Type
Business
Look and feel

```html
<!DOCTYPE html>
<html lang="en">
<head>
<meta charset="utf-8">
<title>Plavorix Business Card</title>
<link rel="stylesheet" href="https://fonts.googleapis.com/css2?family=Archivo:ital,wght@0,800;1,800&family=Montserrat:wght@700&family=Mulish:ital,wght@0,400;1,400&display=swap">
<style>
  :root {
    --backdrop: #2a2a2a;
    --card: #ffffff;
    --orange: #e8541c;
    --ink: #3a3a3a;
    --ink-soft: #555555;
    --band-light: #f2f2f2;
    --band-mid: #c9c9c9;
    --band-dark: #9a9a9a;
  }
  * { box-sizing: border-box; margin: 0; padding: 0; }
  html, body {
    width: 1200px; height: 1200px; overflow: hidden;
    background: var(--backdrop);
  }
  .card {
    position: absolute;
    left: 75px; top: 300px;
    width: 1050px; height: 600px;
    background: var(--card);
    overflow: hidden;
    box-shadow: 0 14px 40px rgba(0,0,0,.45);
  }
  .blueprint-band {
    position: absolute; left: 0; top: 0;
    width: 100%; height: 210px;
    background: linear-gradient(100deg, var(--band-dark) 0%, var(--band-light) 30%, var(--band-mid) 55%, var(--band-light) 80%, var(--band-mid) 100%);
  }
  .accent-stroke {
    position: absolute; left: 0; top: 170px;
    width: 1050px; height: 50px;
  }
  .brand {
    position: absolute; left: 545px; top: 92px;
    display: flex; align-items: center; gap: 14px;
  }
  .brand-dot {
    width: 46px; height: 46px; border-radius: 50%;
    background: var(--orange);
  }
  .brand-name {
    font-family: "Archivo", sans-serif;
    font-weight: 800;
    font-size: 56px;
    line-height: 1;
    color: var(--ink);
    letter-spacing: -0.5px;
  }
  .contact {
    position: absolute; left: 580px; top: 250px;
    font-family: "Mulish", sans-serif;
    color: var(--ink);
  }
  .person-name {
    font-family: "Montserrat", sans-serif;
    font-weight: 700;
    font-size: 34px;
    color: var(--orange);
    line-height: 1.1;
  }
  .person-title {
    font-style: italic;
    font-size: 25px;
    color: var(--ink-soft);
    margin-bottom: 34px;
  }
  .address, .lines {
    font-size: 25px;
    line-height: 1.24;
    list-style: none;
  }
  .address { margin-bottom: 12px; }
  .tagline {
    position: absolute; left: 72px; bottom: 58px;
    font-family: "Archivo", sans-serif;
    font-weight: 800; font-style: italic;
    font-size: 23px; line-height: 1.25;
    color: var(--ink-soft);
  }
</style>
</head>
<body>
  <div class="card">
    <div class="blueprint-band" role="img" aria-label="Photograph of rolled architectural blueprints and drafting sheets"></div>
    <svg class="accent-stroke" viewBox="0 0 1050 50" preserveAspectRatio="none" aria-hidden="true">
      <polygon points="0,34 1050,10 1050,19 0,44" fill="var(--orange)"/>
      <polygon points="0,44 1050,19 1050,50 0,50" fill="var(--card)"/>
    </svg>
    <div class="brand">
      <span class="brand-dot" aria-hidden="true"></span>
      <span class="brand-name">Plavorix</span>
    </div>
    <div class="contact">
      <p class="person-name">Gerald Pinfold</p>
      <p class="person-title">Vice President</p>
      <ul class="address">
        <li>4738 W. Harrowgate Lane. STE 305</li>
        <li>PMB#417 Mesa, AZ 85374</li>
      </ul>
      <ul class="lines">
        <li>866-392-5074 US Toll Free</li>
        <li>123-456-3190 Cell</li>
        <li>gpinfold@plavorix.com</li>
      </ul>
    </div>
    <p class="tagline">Delivering Dependable Drawing Tools<br>for Architects and Engineers<br>Across Every Project Site.</p>
  </div>
</body>
</html>
```